Create a memorable Web Design for real estate branding

we are a Minnepolis brokerage and boutique housing specialist with over 27 years of experience in the Global furnished housing industry, servicing the Greater Los Angeles area. Specializing in “warm environments” we offer a customized approach to satisfying our guests and client’s needs by offering a wide array of options in highly desirable areas. Additionally, Lantern Dwelling Partners offers assistance and expertise to home buyers, sellers and investors.

Industry/Entity Type

Real Estate

Number of Pages Required

1 page

Font styles to use
Serif
Sans Serif
Decorative

```html
<!DOCTYPE html>
<html lang="en">
<head>
<meta charset="utf-8">
<title>Lantern Dwelling Partners</title>
<link rel="stylesheet" href="https://fonts.googleapis.com/css2?family=Raleway:wght@400;500;600;700&family=Nunito+Sans:wght@400;600;700&family=Marcellus+SC&display=swap">
<style>
:root{
  --teal:#13a58b;
  --teal-dark:#0e8f78;
  --green:#7cc242;
  --green-dark:#4f9a2b;
  --ink:#2b2b2b;
  --text:#555;
  --muted:#888;
  --line:#d9d9d9;
  --dark:#1e2226;
  --panel:rgba(40,40,40,.78);
  --gray-bg:#efefef;
  --white:#fff;
}
*{box-sizing:border-box;margin:0;padding:0}
html,body{width:1200px;height:2687px;overflow:hidden;background:var(--white)}
body{font-family:"Nunito Sans",Arial,sans-serif;color:var(--text);position:relative}
.abs{position:absolute}
.ph{position:absolute}

/* header + hero */
.hero{left:0;top:0;width:1200px;height:616px;background:linear-gradient(135deg,#cfc9bd 0%,#e9e6e0 35%,#b9b3a7 60%,#8a8680 100%)}
.topbar{left:0;top:0;width:1200px;height:129px;background:linear-gradient(rgba(20,20,20,.88),rgba(20,20,20,.72))}
.brand{left:102px;top:40px;font-family:"Raleway",sans-serif;font-weight:700;color:var(--green);font-size:30px;line-height:34px;width:300px}
.consult{left:815px;top:0;width:268px;height:36px;background:var(--teal);color:#fff;border:2px solid #7de0c8;font-family:"Marcellus SC",serif;font-size:16px;display:flex;align-items:center;justify-content:center}
.contact-top{right:110px;top:50px;display:flex;gap:22px;align-items:center;color:#fff;font-size:13px}
.contact-top .phone{font-size:21px}
.contact-top span{display:flex;align-items:center;gap:8px}
.nav{left:433px;top:87px;display:flex;font-family:"Marcellus SC",serif;font-size:16px;color:#fff}
.nav a{padding:0 16px;border-left:1px solid rgba(255,255,255,.4);text-decoration:none;color:#fff}
.nav a:first-child{border:0;padding-left:0;color:var(--teal)}
.arrow{top:342px;width:34px;height:32px;background:#222;display:flex;align-items:center;justify-content:center}

.tabs{left:102px;top:424px;display:flex;gap:3px}
.tabs span{background:var(--green);color:#1a1a1a;font-size:16px;padding:8px 20px;height:34px}
.tabs span:first-child{background:var(--teal);color:#111}
.search{left:102px;top:458px;width:663px;height:151px;background:var(--panel);border-radius:0 8px 8px 8px}
.search input,.field{position:absolute;background:#fff;border:0;font-size:14px;color:#444;padding:0 10px;display:flex;align-items:center;font-family:inherit}
.search .go{position:absolute;left:548px;top:22px;width:90px;height:36px;background:#3a3a3a;color:#fff;font-size:14px;display:flex;align-items:center;justify-content:center}
.search label{position:absolute;top:75px;color:#fff;font-size:12px}
.field{top:99px;width:147px;height:31px;font-size:12px;justify-content:space-between}
.field::after{content:"";border:6px solid transparent;border-top-color:var(--green);margin-top:6px}

/* about */
.about-photo{left:102px;top:659px;width:236px;height:270px;background:linear-gradient(160deg,#e6ecf2,#9aa7b4 60%,#4a4f57)}
.h2{font-family:"Raleway",sans-serif;font-weight:600;color:var(--ink);font-size:22px}
.about-title{left:351px;top:653px;width:397px;padding-bottom:8px;border-bottom:2px solid var(--line)}
.about-body{left:351px;top:700px;width:395px;font-size:13px;line-height:20px}
.ticks{left:351px;top:771px;width:395px;list-style:none;font-size:12px;line-height:17px}
.ticks li{display:flex;gap:10px;margin-bottom:8px}
.ticks svg{flex:none;margin-top:3px}
.btn{background:var(--teal);color:#fff;font-size:12px;display:flex;align-items:center;justify-content:center}
.read{left:351px;top:897px;width:104px;height:37px}
.offer-title{left:795px;top:653px;width:305px;padding-bottom:8px;border-bottom:2px solid var(--line);font-size:20px}
.offer{left:795px;width:300px;display:flex;gap:14px}
.offer .ic{width:40px;height:40px;border:1px solid var(--green);flex:none;display:flex;align-items:center;justify-content:center}
.offer b{display:block;color:var(--ink);font-size:12px;margin-bottom:4px}
.offer p{font-size:11px;line-height:16px}

/* featured */
.city{left:0;top:978px;width:1200px;height:276px;background:linear-gradient(#3b4147,#1d2228)}
.feat-title{left:0;top:1015px;width:1200px;text-align:center;color:#fff;font-family:"Raleway",sans-serif;font-size:23px}
.rule{height:2px;background:var(--line)}
.rule::after{content:"";display:block;width:40px;height:2px;margin:0 auto;background:var(--teal)}
.card{top:1110px;width:227px;height:305px;background:#fff;border:1px solid var(--line)}
.card .ph{left:7px;top:7px;width:212px;height:127px}
.card h3{position:absolute;left:12px;top:150px;font-size:14px;font-weight:400;color:var(--ink)}
.card .sub{position:absolute;left:12px;top:178px;font-size:12px;color:var(--muted)}
.card .tag{position:absolute;left:8px;top:225px;height:26px;padding:0 12px;font-size:12px;color:#fff;display:flex;align-items:center}
.card .price{position:absolute;right:10px;top:222px;font-size:22px;color:#2d9fc9}
.card .meta{position:absolute;left:0;bottom:0;width:100%;height:40px;border-top:1px solid var(--line);display:flex;font-size:10px;color:var(--muted)}
.card .meta span{flex:1;display:flex;align-items:center;justify-content:center;border-right:1px solid var(--line)}
.card .meta span:last-child{border:0}
.t-rent{background:var(--teal)}
.t-sold{background:#333}

/* cta band */
.cta{left:0;top:1465px;width:1200px;height:79px;background:var(--teal)}
.cta p{position:absolute;left:113px;top:13px;color:#fff;font-family:"Raleway",sans-serif;font-weight:600;font-size:19px;line-height:26px;width:720px}
.cta .call{position:absolute;left:903px;top:14px;width:191px;height:54px;background:#2f3537;border-radius:4px;color:#fff;text-align:center;font-size:14px;line-height:18px;padding-top:6px}
.cta .call strong{display:block;font-size:22px;font-weight:400;line-height:26px}

/* looking for */
.look-title{left:0;top:1606px;width:1200px;text-align:center}
.look{width:385px;text-align:center}
.look .ph{position:static;height:256px}
.look h4{font-weight:400;font-size:17px;color:var(--ink);margin:20px 0 8px}
.look p{font-size:13.5px;line-height:21px;color:#444}

/* refer + newsletter */
.refer{left:0;top:2081px;width:578px;height:203px;background:var(--gray-bg)}
.news{left:594px;top:2081px;width:606px;height:203px;background:var(--gray-bg)}
.panel-h{position:absolute;display:flex;align-items:center;gap:12px;font-family:"Raleway",sans-serif;font-weight:600;font-size:22px;color:var(--ink)}
.inp{position:absolute;background:#fff;border:1px solid #ccc;font-size:12px;color:#444;display:flex;align-items:center;padding-left:12px}
.send{position:absolute;color:#fff;background:var(--teal);font-size:18px;display:flex;align-items:center;justify-content:center}

/* footer */
.footer{left:0;top:2284px;width:1200px;height:363px;background:linear-gradient(#2a3036,#15191d)}
.fh{position:absolute;top:86px;font-family:"Marcellus SC",serif;font-size:19px;color:#fff}
.fh em{font-style:normal;color:var(--green)}
.links{position:absolute;left:102px;top:132px;list-style:none;color:#fff;font-size:12px}
.links li{height:37px}
.links li::before{content:"›";margin-right:10px}
.cd{position:absolute;left:312px;display:flex;gap:16px;color:#fff;font-size:13px;line-height:19px}
.cd .ic{width:28px;height:28px;background:var(--green);flex:none;display:flex;align-items:center;justify-content:center}
.soc{position:absolute;left:625px;display:flex;align-items:center;gap:18px;color:#fff;font-size:11px}
.soc i{width:36px;height:36px;border-radius:50%;display:block}
.foot-brand{left:824px;top:2450px;font-family:"Raleway",sans-serif;font-weight:700;color:var(--green);font-size:30px;line-height:34px;width:280px;text-align:right}
.copy{left:0;top:2647px;width:1200px;height:40px;background:var(--teal-dark);color:#fff;font-size:13px;display:flex;align-items:center;justify-content:center}
</style>
</head>
<body>

<!-- hero -->
<div class="ph hero" role="img" aria-label="Photo of a bright modern kitchen with granite counters and glass doors"></div>
<header class="abs topbar"></header>
<div class="abs brand">Lantern Dwelling Partners</div>
<div class="abs consult">Schedule Free Consultation</div>
<div class="abs contact-top">
  <span><svg width="16" height="12" viewBox="0 0 16 12"><rect width="16" height="12" rx="1" fill="#7cc242"/><path d="M0 1l8 6 8-6" stroke="#222" fill="none"/></svg>hello@lanterndwelling.example</span>
  <span class="phone"><svg width="18" height="18" viewBox="0 0 24 24"><path d="M6.6 10.8a15 15 0 0 0 6.6 6.6l2.2-2.2c.3-.3.7-.4 1-.2 1.1.4 2.3.6 3.6.6.6 0 1 .4 1 1V20c0 .6-.4 1-1 1A17 17 0 0 1 3 4c0-.6.4-1 1-1h3.5c.6 0 1 .4 1 1 0 1.3.2 2.5.6 3.6.1.3 0 .7-.2 1z" fill="#7cc242"/></svg>123-456-7890</span>
</div>
<nav class="abs nav"><a>Find a Home</a><a>Sell Your Home</a><a>Lantern Blog</a><a>Our Agents</a><a>Contact Us</a></nav>
<div class="abs arrow" style="left:0"><svg width="10" height="14"><path d="M8 1L2 7l6 6" stroke="#fff" stroke-width="2" fill="none"/></svg></div>
<div class="abs arrow" style="right:0"><svg width="10" height="14"><path d="M2 1l6 6-6 6" stroke="#fff" stroke-width="2" fill="none"/></svg></div>

<div class="abs tabs"><span>For Sale</span><span>To Rent</span><span>Developments</span><span>Map Search</span></div>
<form class="abs search">
  <div class="field" style="left:16px;top:22px;width:522px;height:36px;font-size:14px">Find property for sale in Minneapolis</div>
  <div class="go">SEARCH</div>
  <label style="left:16px">Property Type</label>
  <label style="left:174px">Price Range</label>
  <label style="left:489px">Beds</label>
  <div class="field" style="left:16px">Any</div>
  <div class="field" style="left:174px">For Any</div>
  <div class="field" style="left:331px">To Any</div>
  <div class="field" style="left:489px">Any</div>
</form>

<!-- about -->
<div class="ph about-photo" role="img" aria-label="Photo of an agent in a suit meeting a client at a desk"></div>
<h2 class="abs h2 about-title">About Lantern Dwelling Partners</h2>
<p class="abs about-body">Lorem ipsum dolor sit amet, consectetuer adipiscing elit, sed diam nonummy nibh euismod tincidunt ut laoreet dore magna aliquam erat volutpat. Ut wisi enim ad minim.</p>
<ul class="abs ticks">
  <li><svg width="12" height="10"><path d="M1 5l3 3 7-7" stroke="#333" stroke-width="2" fill="none"/></svg>we are a Minneapolis brokerage and boutique housing specialist with over 27 years of experience</li>
  <li><svg width="12" height="10"><path d="M1 5l3 3 7-7" stroke="#333" stroke-width="2" fill="none"/></svg>Specializing in “warm environments”</li>
  <li><svg width="12" height="10"><path d="M1 5l3 3 7-7" stroke="#333" stroke-width="2" fill="none"/></svg>we offer a customized approach to satisfying our guests and client’s needs by offering a wide array of options in highly desirable areas</li>
</ul>
<div class="abs btn read">READ MORE</div>

<h2 class="abs h2 offer-title">Offers Assistance &amp; Expertise To</h2>
<div class="abs offer" style="top:710px"><div class="ic"><svg width="22" height="22"><circle cx="11" cy="11" r="9" fill="#7cc242"/></svg></div><div><b>Buyers</b><p>Lorem ipsum dolor sit amet, consectetuer adipiscing elit, sed dianonummy nibh</p></div></div>
<div class="abs offer" style="top:790px"><div class="ic"><svg width="22" height="22"><rect x="2" y="6" width="18" height="10" rx="3" fill="#7cc242"/></svg></div><div><b>Sellers</b><p>Lorem ipsum dolor sit amet, consectetuer adipiscing elit, sed dianonum</p></div></div>
<div class="abs offer" style="top:876px"><div class="ic"><svg width="22" height="22"><circle cx="11" cy="7" r="5" fill="#7cc242"/><rect x="3" y="13" width="16" height="8" rx="4" fill="#7cc242"/></svg></div><div><b>Investors</b><p>Lorem ipsum dolor sit amet, consectetuer adi elit, sed dianonummy nibh euismod</p></div></div>

<!-- featured -->
<section class="ph city" role="img" aria-label="Dimmed photo of a city skyline"></section>
<h2 class="abs feat-title">Featured Property Listings</h2>
<div class="abs rule" style="left:403px;top:1061px;width:394px"></div>

<article class="abs card" style="left:102px"><div class="ph" role="img" aria-label="Photo of a stone family house" style="background:linear-gradient(#9fc3e4,#c8c3b8 55%,#6e8a4c)"></div><h3>123 Dollar Smit Amet</h3><span class="sub">Duis autem vel eum iriure</span><span class="tag t-rent">For Rent</span><span class="price">$ 123</span><div class="meta"><span>1200 sq ft</span><span>2 Beds</span><span>2 Baths</span></div></article>
<article class="abs card" style="left:358px"><div class="ph" role="img" aria-label="Photo of a modern living room with a red wall" style="background:linear-gradient(90deg,#c9d2dc,#b43a2e 55%,#8aa0b6)"></div><h3>123 Dollar Smit Amet</h3><span class="sub">Duis autem vel eum iriure</span><span class="tag t-sold">Sold</span><span class="price">$ 213</span><div class="meta"><span>1200 sq ft</span><span>2 Beds</span><span>2 Baths</span></div></article>
<article class="abs card" style="left:614px"><div class="ph" role="img" aria-label="Photo of a bright apartment lounge" style="background:linear-gradient(#d9e4ec,#8fa7b8 60%,#6a7d8c)"></div><h3>123 Dollar Smit Amet</h3><span class="sub">Duis autem vel eum iriure</span><span class="tag t-sold">For Rent</span><span class="price">$ 143</span><div class="meta"><span>1200 sq ft</span><span>2 Beds</span><span>2 Baths</span></div></article>
<article class="abs card" style="left:870px"><div class="ph" role="img" aria-label="Photo of a dark grey two-storey house" style="background:linear-gradient(#b8d4ea,#4a5460 55%,#5e7a3f)"></div><h3>123 Dollar Smit Amet</h3><span class="sub">Duis autem vel eum iriure</span><span class="tag t-sold">For Sell</span><span class="price">$ 132</span><div class="meta"><span>1200 sq ft</span><span>2 Beds</span><span>2 Baths</span></div></article>

<!-- cta -->
<section class="abs cta">
  <p>Sed ut perspiciatis unde omnis iste natus error sit Accusant doloremque lorems ispum monis laudantium, totamrem aperiam, moregi eaquemn.</p>
  <div class="call">Call Us Today<strong>123-456-7890</strong></div>
</section>

<!-- looking for -->
<h2 class="abs h2 look-title">What Are You Looking For</h2>
<div class="abs rule" style="left:403px;top:1642px;width:394px"></div>
<div class="abs look" style="left:165px;top:1687px"><div class="ph" role="img" aria-label="Photo of a modern lounge with orange ceiling discs" style="background:linear-gradient(#c98a4a,#d9d3c9 40%,#8a6a4a)"></div><h4>BUYING A PROPERTY</h4><p>Lorem ipsum dolor sit amet, consectetuer adipiscing elit, sed diam nonummy nibh euismod tincidunt ut laoreet dolore magna aliquam erat volutpat. Ut wisi enim ad minim veniam,</p></div>
<div class="abs look" style="left:654px;top:1687px"><div class="ph" role="img" aria-label="Photo of a couple shaking hands with an agent outside a house" style="background:linear-gradient(#9bb7d4,#c9c2b4 45%,#5f8a3c)"></div><h4>SELLING A PROPERTY</h4><p>Lorem ut wisi enim ad minim veniam, quis nostrm ci tation ullamcorper suscipit lobol rtis nisl ut aliquip ex ea ad commo erat volutpat. Ut wisi enim ad minim veniam,</p></div>

<!-- refer + newsletter -->
<section class="abs refer">
  <div class="panel-h" style="left:102px;top:26px"><svg width="34" height="30" viewBox="0 0 34 30"><rect x="2" y="8" width="20" height="20" fill="none" stroke="#7cc242" stroke-width="3"/><path d="M12 18c2-8 8-11 14-11V2l7 8-7 8v-5c-6 0-10 2-14 5z" fill="#7cc242"/></svg>Refer A Friend</div>
  <div class="inp" style="left:102px;top:65px;width:215px;height:40px">From*</div>
  <div class="inp" style="left:328px;top:65px;width:218px;height:40px">To*</div>
  <div class="inp" style="left:102px;top:111px;width:364px;height:40px">Message (Optional)</div>
  <div class="send" style="left:464px;top:111px;width:82px;height:40px">Send</div>
  <span class="abs" style="left:110px;top:163px;font-size:11px;color:#444">*Privacy Policy</span>
</section>
<section class="abs news">
  <div class="panel-h" style="left:26px;top:26px"><svg width="34" height="30" viewBox="0 0 34 30"><path d="M2 12L17 2l15 10v16H2z" fill="#7cc242"/><path d="M2 12l15 10 15-10" stroke="#fff" stroke-width="2" fill="none"/></svg>Join Our newsletter for exclusive deals</div>
  <p class="abs" style="left:26px;top:76px;width:480px;font-size:11px;line-height:18px;color:#444">Lorem ut wisi enim ad minim veniam, quis nostrm ci tation ullamcorper suscipit lobol rtis nisl ut aliquip ex ea ad commo.</p>
  <div class="inp" style="left:26px;top:128px;width:200px;height:42px">Email Address</div>
  <div class="send" style="left:222px;top:128px;width:134px;height:48px;font-size:19px">Subscribe</div>
</section>

<!-- footer -->
<footer class="ph footer" role="img" aria-label="Dimmed photo of a city skyline behind the footer">
  <h3 class="fh" style="left:102px">Quick <em>Links</em></h3>
  <ul class="links"><li>Find A Home</li><li>Sell Your Home</li><li>Lantern Blog</li><li>Our Agents</li><li>Contact Us</li></ul>
  <h3 class="fh" style="left:312px">Contact <em>Details</em></h3>
  <div class="cd" style="top:124px"><span class="ic"><svg width="12" height="16"><path d="M6 0a6 6 0 0 1 6 6c0 4-6 10-6 10S0 10 0 6a6 6 0 0 1 6-6z" fill="#fff"/><circle cx="6" cy="6" r="2" fill="#7cc242"/></svg></span><div><b>Office:</b><br>123, Lorem ipsum dolor<br>sit amet, consecte 32145</div></div>
  <div class="cd" style="top:206px;align-items:center"><span class="ic"><svg width="14" height="14" viewBox="0 0 24 24"><path d="M6.6 10.8a15 15 0 0 0 6.6 6.6l2.2-2.2c.3-.3.7-.4 1-.2 1.1.4 2.3.6 3.6.6.6 0 1 .4 1 1V20c0 .6-.4 1-1 1A17 17 0 0 1 3 4c0-.6.4-1 1-1h3.5c.6 0 1 .4 1 1 0 1.3.2 2.5.6 3.6.1.3 0 .7-.2 1z" fill="#fff"/></svg></span>123 456 7890</div>
  <div class="cd" style="top:266px;align-items:center"><span class="ic"><svg width="14" height="10"><rect width="14" height="10" fill="#fff"/><path d="M0 0l7 5 7-5" stroke="#7cc242" fill="none"/></svg></span>hello@lanterndwelling.example</div>
  <h3 class="fh" style="left:623px">Follow <em>Us</em></h3>
  <div class="soc" style="top:118px"><i style="background:#2f5aa0"></i>FACEPAGE</div>
  <div class="soc" style="top:168px"><i style="background:#2aa4d8"></i>CHIRPER</div>
  <div class="soc" style="top:218px"><i style="background:#1b75b0"></i>LINKWORK</div>
  <div class="soc" style="top:268px"><i style="background:#d04a35"></i>CIRCLES PLUS</div>
</footer>
<div class="abs foot-brand">Lantern Dwelling Partners</div>
<div class="abs copy">Copyright © 2016 Lantern Dwelling Partners. All rights reserved.</div>

</body>
</html>
```